Redesign to improve branding visibility and product messaging

Update the logo using the new logo provided attached.
Then, improve product messaging on the packaging, however leaving the colours, general blurbs, and the fruit/nut image outlines as they are (but open to make it simpler).
Please review photos Stockist 1" to 5" and recommend the new style for:
1 Energy Ball Bag
1 Energy Ball Inner Box
1 Cereal Bag
Key features:
1. Allow more transparent window to show more of the product inside.
2. Strong brand presence and clear nutritional call outs - keep in mind we display our products on supermarket shelves.
3. Product Messaging:
- 1st priority: Product Name
- 2nd priority: Nutritional call outs (All natural, GF, Vegan, High Fibre, No added sugar, etc.). This info is available in the current packaging and more info on the website.
- 3rd priority: Ingredients on front cover (example: 7 ingredients only: x1, x2, x3, x4, x5, x6, x7.)
- 4th priority: Locally Made by a nutritionist.
- 5th priority: Sugar content in the nutritional panel to say: From Healthy Natural Sources
Tips:
1. Use Style 1 as benchmark.
2. Use the other image references as follows:
Style 2 and 5 = Try do something similar for the energy ball bags.
Style 4 = Maybe add the line up of other flavours on the back or the side of the packaging for the energy ball box and the cereal bags.
Style 7 = Do something similar with regards to the use of real imagery on the packaging as if you can pick out the product right of the packaging. Note also how they list the ingredients on the front of packaging.
Style 8 = Do something similar - be proud about the real ingredients used.
Style 9 = An example of how much transparent area we can do, please suggest a nice unique transparent shape.
Style 10 = copy the way it communicates the health benefits very clearly.

```html
<!DOCTYPE html>
<html lang="en">
<head>
<meta charset="utf-8">
<title>Wren Nutrition – Apricot &amp; Coconut Energy Balls Bag</title>
<link href="https://fonts.googleapis.com/css2?family=Montserrat:wght@400;500;600;700;800&family=Mr+Dafoe&display=swap" rel="stylesheet">
<style>
  :root{
    --rose:#d6a6ab;
    --rose-deep:#c58b92;
    --rose-pale:#ead0d3;
    --rose-line:#d59aa2;
    --ink:#232323;
    --grey:#8a8a8a;
    --white:#ffffff;
    --stage:#efefef;
    --ball-light:#f3e6d6;
    --ball-mid:#e2bf97;
  }
  *{box-sizing:border-box;margin:0;padding:0}
  html,body{width:903px;height:1200px;overflow:hidden}
  body{background:var(--stage);font-family:'Montserrat',sans-serif;color:var(--ink);position:relative}

  .bag{position:absolute;left:72px;width:758px;height:500px;background:var(--white);overflow:hidden;box-shadow:0 6px 18px rgba(0,0,0,.12)}
  .bag--back{top:40px}
  .bag--front{top:640px}
  .bag__band{position:absolute;left:0;right:0;top:0;height:270px;background:var(--rose)}
  .bag__crimp{position:absolute;top:0;bottom:0;width:22px;z-index:5;
    background:repeating-linear-gradient(90deg,rgba(255,255,255,.55) 0 2px,rgba(0,0,0,.06) 2px 4px)}
  .bag__crimp--left{left:0}
  .bag__crimp--right{right:0}
  .bag__seal{position:absolute;left:0;right:0;top:262px;height:10px;background:linear-gradient(180deg,var(--rose-deep),var(--rose))}

  .photo{position:absolute;border-radius:50%;background:radial-gradient(circle at 40% 35%,var(--ball-light),var(--ball-mid) 75%,#d7ad82)}
  .illustration{position:absolute;border-radius:50%}

  /* back panel */
  .section-title{position:absolute;font-weight:600;font-size:19px;letter-spacing:.5px;color:var(--white);line-height:1.2}
  .section-title strong{color:var(--ink);font-weight:700}
  .description-box{position:absolute;left:208px;top:90px;width:320px;height:118px;border:1px solid rgba(60,40,40,.45);border-radius:6px}
  .description{position:absolute;left:277px;top:115px;width:230px;font-size:8.4px;line-height:10.5px;color:var(--white);font-weight:500}
  .benefits{position:absolute;left:543px;top:114px;list-style:none;font-size:8.8px;font-weight:600;line-height:10.6px;color:var(--ink)}
  .benefits li::before{content:"· "}
  .origin-badge{position:absolute;left:544px;top:176px;width:120px;height:32px;border:2px solid #2d7a3a;border-radius:3px;background:var(--white)}
  .recycle{position:absolute;left:680px;top:178px}

  .nutrition-panel{position:absolute;left:65px;top:292px;width:188px;height:158px;border:2px solid var(--ink);border-radius:8px;background:var(--white)}
  .nutrition-panel h3{font-size:11.5px;font-weight:600;text-align:center;padding:8px 0 6px;border-bottom:1px solid #ddd}
  .nutrition-panel table{width:150px;margin:14px 0 0 20px;border-collapse:collapse;font-size:6.6px}
  .nutrition-panel td{height:10.4px;font-weight:500}
  .nutrition-panel td:last-child{text-align:right}

  .label-heading{position:absolute;font-size:11.5px;font-weight:600;color:#555}
  .label-body{position:absolute;font-size:8.2px;font-weight:600;line-height:10px;color:#555}
  .rule{position:absolute;left:291px;top:379px;width:166px;height:1px;background:#444}
  .storage-heading{color:var(--rose-line)}
  .kitchen{position:absolute;left:542px;top:282px;font-size:7.8px;line-height:9.8px;color:#444}
  .kitchen strong{font-weight:700;color:var(--ink)}

  /* front panel */
  .brand-name{position:absolute;left:254px;top:118px;width:280px;text-align:center;font-size:15px;font-weight:600;letter-spacing:2px;color:var(--white);line-height:1.3}
  .product-name{position:absolute;left:150px;top:203px;width:460px;text-align:center;font-size:35px;font-weight:800;letter-spacing:-.5px;color:var(--ink)}
  .product-type{position:absolute;left:210px;top:222px;width:340px;text-align:center;font-family:'Mr Dafoe',cursive;font-size:60px;color:var(--white);line-height:1}
  .claims{position:absolute;left:262px;top:304px;display:flex;gap:9px;list-style:none}
  .claims li{width:40px;text-align:center;font-size:5px;font-weight:500;color:#555;line-height:6px}
  .claims svg{display:block;margin:0 auto 4px}
  .local-mark{position:absolute;left:86px;top:234px;width:58px;height:58px;border:1.5px solid #333;border-radius:50%}
  .maker-note{position:absolute;right:82px;top:318px;text-align:right;font-size:9px;font-weight:600;line-height:11px;color:var(--white)}
  .net-weight{position:absolute;right:82px;top:364px;font-size:17px;font-weight:800;color:var(--white)}
  .net-weight span{font-weight:500}
  .ingredient-callout{position:absolute;left:183px;top:408px;width:400px;text-align:center}
  .ingredient-callout h4{font-size:11.5px;font-weight:700;letter-spacing:.3px}
  .ingredient-callout p{font-size:7.6px;line-height:9.5px;color:var(--grey);margin-top:5px;letter-spacing:.3px}
</style>
</head>
<body>

<!-- Back of bag -->
<section class="bag bag--back">
  <div class="bag__band"></div>
  <div class="bag__seal"></div>
  <div class="bag__crimp bag__crimp--left"></div>
  <div class="bag__crimp bag__crimp--right"></div>

  <div class="photo" style="left:22px;top:17px;width:216px;height:216px" role="img" aria-label="Close-up of a coconut-rolled energy ball"></div>

  <h2 class="section-title" style="left:277px;top:57px">PRODUCT <strong>DESCRIPTION</strong></h2>
  <div class="description-box"></div>
  <p class="description">Clean energy made from real whole foods.<br>Our energy balls are crafted using only natural ingredients to provide sustained energy, fibre and nutrients without any added sugar.<br>Perfect for a healthy snack, pre-workout boost or mid-day energy.</p>

  <h2 class="section-title" style="left:543px;top:55px">KEY BENEFITS<br>SECTION</h2>
  <ul class="benefits">
    <li>Plant Based Energy</li>
    <li>Naturally Sweetened with Dates</li>
    <li>High in Fibre</li>
    <li>No Artificial Ingredients</li>
    <li>No Added Sugar</li>
  </ul>
  <div class="origin-badge" role="img" aria-label="Country of origin badge"></div>
  <svg class="recycle" width="32" height="30" viewBox="0 0 32 30" aria-label="Recyclable">
    <g fill="none" stroke="#fff" stroke-width="3" stroke-linejoin="round">
      <path d="M11 6 L16 2 L21 10"/><path d="M25 14 L28 24 L18 24"/><path d="M10 26 L3 24 L8 14"/>
    </g>
  </svg>

  <div class="photo" style="left:362px;top:178px;width:130px;height:130px;z-index:2" role="img" aria-label="Single coconut energy ball"></div>

  <div class="nutrition-panel">
    <h3>NUTRITION PANEL</h3>
    <table>
      <tr><td>ENERGY</td><td>1G</td></tr>
      <tr><td>PROTEIN</td><td>1G</td></tr>
      <tr><td>FAT - TOTAL</td><td>1G</td></tr>
      <tr><td>FAT - SATURATED</td><td>1G</td></tr>
      <tr><td>CARBOHYDRATES</td><td>1G</td></tr>
      <tr><td>TOTAL</td><td>1G</td></tr>
      <tr><td>SUGARS</td><td>1G</td></tr>
      <tr><td>DIETARY FIBRE</td><td>1G</td></tr>
      <tr><td>SODIUM</td><td>1G</td></tr>
    </table>
  </div>

  <h3 class="label-heading" style="left:291px;top:316px">INGREDIENTS:</h3>
  <p class="label-body" style="left:291px;top:340px">Dates, Almonds, Cacao Powder,<br>Coconut, Chia Seeds, Sea Salt,<br>Natural Vanilla Extract.</p>
  <div class="rule"></div>
  <h3 class="label-heading storage-heading" style="left:291px;top:397px">STORAGE</h3>
  <p class="label-body" style="left:291px;top:418px">Store in a cool dry place.<br>Reseal after opening.</p>

  <p class="kitchen"><strong>JOIN US IN THE KITCHEN</strong><br>View more healthy recipes<br>#WRENKITCHEN<br>@WRENNUTRITION</p>

  <div class="illustration" style="left:480px;top:326px;width:234px;height:200px;background:radial-gradient(circle at 50% 45%,rgba(234,208,211,.55),rgba(213,154,162,.35))" role="img" aria-label="Line drawing of a coconut and an almond"></div>
</section>

<!-- Front of bag -->
<section class="bag bag--front">
  <div class="bag__band"></div>
  <div class="bag__crimp bag__crimp--left"></div>
  <div class="bag__crimp bag__crimp--right"></div>

  <div class="photo" style="left:14px;top:-2px;width:216px;height:216px" role="img" aria-label="Close-up of a coconut energy ball"></div>
  <div class="photo" style="left:580px;top:20px;width:172px;height:172px" role="img" aria-label="Coconut energy ball at the bag edge"></div>

  <div class="illustration" style="left:212px;top:54px;width:334px;height:315px;background:radial-gradient(circle at 55% 60%,#e6c3a4,#c98f96 60%,#d8a6ab)" role="img" aria-label="Coconut drawing framing an energy ball seen through the window"></div>

  <p class="brand-name">WREN<br>NUTRITION</p>
  <h1 class="product-name">APRICOT &amp; COCONUT</h1>
  <p class="product-type">Energy balls</p>

  <ul class="claims">
    <li><svg width="36" height="36" viewBox="0 0 36 36"><circle cx="18" cy="18" r="16" fill="#fff" stroke="#555"/><rect x="12" y="12" width="12" height="12" fill="none" stroke="#555"/><line x1="8" y1="28" x2="28" y2="8" stroke="#555"/></svg>NO ADDED SUGAR</li>
    <li><svg width="36" height="36" viewBox="0 0 36 36"><circle cx="18" cy="18" r="16" fill="#fff" stroke="#555"/><path d="M12 24 Q18 10 24 12 Q20 24 12 24Z" fill="none" stroke="#555"/></svg>HIGH FIBRE</li>
    <li><svg width="36" height="36" viewBox="0 0 36 36"><circle cx="18" cy="18" r="16" fill="#fff" stroke="#555"/><path d="M18 8 V28 M18 14 l-4 -3 M18 14 l4 -3 M18 19 l-4 -3 M18 19 l4 -3" stroke="#555" fill="none"/><line x1="9" y1="27" x2="27" y2="9" stroke="#555"/></svg>GLUTEN FREE</li>
    <li><svg width="36" height="36" viewBox="0 0 36 36"><circle cx="18" cy="18" r="16" fill="#fff" stroke="#555"/><rect x="10" y="20" width="16" height="6" fill="none" stroke="#555"/><path d="M13 20 Q14 12 18 12 Q22 12 23 20" fill="none" stroke="#555"/></svg>VEGAN</li>
    <li><svg width="36" height="36" viewBox="0 0 36 36"><circle cx="18" cy="18" r="16" fill="#fff" stroke="#555"/><path d="M18 26 V15 M18 18 Q12 16 13 11 Q18 12 18 18 M18 16 Q23 13 24 9" fill="none" stroke="#555"/><line x1="11" y1="26" x2="25" y2="26" stroke="#555"/></svg>ALL NATURAL</li>
  </ul>

  <div class="local-mark" role="img" aria-label="Locally made badge"></div>

  <div class="photo" style="left:46px;top:307px;width:174px;height:147px;border-radius:45%" role="img" aria-label="Three coconut energy balls stacked"></div>

  <div class="illustration" style="left:532px;top:231px;width:214px;height:223px;background:radial-gradient(circle at 45% 55%,#dba9a9,#c98f96 70%)" role="img" aria-label="Coconut drawing over a close-up of coconut texture"></div>
  <p class="maker-note">CREATED<br>BY A NUTRITIONIST<br>MADE LOCALLY</p>
  <p class="net-weight">40GM <span>NET</span></p>

  <div class="ingredient-callout">
    <h4>ONLY 7 REAL INGREDIENTS</h4>
    <p>DATES - ALMONDS - CACAO - COCONUT<br>CHIA SEEDS - SEA SALT - VANILLA</p>
  </div>
</section>

</body>
</html>
```